Design and Renovation Company Luxury Business Card

I want to create a luxury business card for a Design and Renovation Firm . We will use our current logo. The company name is 528BUILDA. We do not want anything standard. We need a very unique concept.
Please see uploaded inspiration. I really like the textured paper option. I would like the card to be thick with debossing, and/or embossing options. The logo has orange in it but I would like to see the card with and without the orange. I think the orange may make the company feel less high-end. The goal is to elevate the logo not match its vibe per se of the logo. We want something very unique, not standard at all!
I would like a space for :
Logo,
Name,
Position,
Email,
Office number,
Website Address,
Business Address,
Thank you!
Have fun!
Target Market(s)
Home owners Age 35 +
Industry/Entity Type
Design and Renovation
Contact Information for Business Card
Logo, Name, Position, Email, Office number, Website Address, Business Address,.
Colors
Designer to choose colors to be used in the design.
Requirements
Must have
- A luxury designer feel. Must be black or dark grey but open to other luxury ideas.
Nice to have
- Gold, silver, black embossing or debossing. Textured paper design.
Should not have
- A cheap look and feel.

```html
<!DOCTYPE html>
<html lang="en">
<head>
<meta charset="utf-8">
<title>528BUILDA Business Card</title>
<link rel="stylesheet" href="https://fonts.googleapis.com/css2?family=Montserrat:wght@400;600&display=swap">
<style>
  :root {
    --backdrop: #5e4b39;
    --card-light: #ffffff;
    --card-dark: #1a1a1a;
    --ink: #111111;
    --accent: #f7941d;
    --paper-text: #ffffff;
  }
  * { margin: 0; padding: 0; box-sizing: border-box; }
  html, body { width: 900px; height: 1200px; overflow: hidden; }
  body {
    background: var(--backdrop);
    position: relative;
    font-family: "Montserrat", Arial, sans-serif;
  }
  .card {
    position: absolute;
    border-radius: 22px;
    overflow: hidden;
  }
  .card--front {
    left: 80px; top: 131px; width: 742px; height: 440px;
    background: var(--card-light);
    color: var(--ink);
  }
  .card--back {
    left: 78px; top: 638px; width: 744px; height: 442px;
    background: var(--card-dark);
    color: var(--paper-text);
  }
  .company-name {
    position: absolute;
    font-family: "Montserrat", Arial, sans-serif;
    font-weight: 600;
    white-space: nowrap;
    line-height: 1;
  }
  .card--front .company-name { left: 42px; top: 62px; font-size: 38px; color: var(--ink); }
  .card--back .company-name {
    left: 0; right: 0; top: 190px; text-align: center;
    font-size: 62px; color: var(--paper-text);
  }

  .person { position: absolute; right: 57px; top: 48px; text-align: right; }
  .person__name { font-weight: 600; font-size: 26px; color: var(--accent); line-height: 1.1; }
  .person__role { font-size: 16px; margin-top: 6px; }

  .address { position: absolute; left: 35px; top: 268px; font-size: 16px; line-height: 20px; font-style: normal; }
  .contact-list { position: absolute; left: 35px; top: 334px; list-style: none; font-size: 16px; }
  .contact-list li { display: flex; align-items: center; height: 20px; margin-bottom: 8px; }
  .contact-list svg { width: 16px; height: 16px; margin-right: 9px; flex: none; }
</style>
</head>
<body>
  <section class="card card--front" aria-label="Business card front">
    <p class="company-name">528BUILDA</p>
    <div class="person">
      <p class="person__name">Daniel Brooks</p>
      <p class="person__role">Managing Director</p>
    </div>
    <address class="address">
      415 Maple Grove Ave, #112<br>Fairview, OH 430517
    </address>
    <ul class="contact-list">
      <li>
        <svg viewBox="0 0 16 16" aria-hidden="true"><path fill="var(--accent)" d="M3.6 1.5l2.3 2.8-1.4 1.6c.9 2 2.6 3.7 4.6 4.6l1.6-1.4 2.8 2.3-1.3 2.3C7.4 13.5 2.5 8.6 2.3 3z"/></svg>
        555-318-0192
      </li>
      <li>
        <svg viewBox="0 0 16 16" aria-hidden="true"><rect x="1.5" y="3.5" width="13" height="9" rx="1" fill="var(--accent)"/><path d="M2 4l6 5 6-5" fill="none" stroke="#fff" stroke-width="1.2"/></svg>
        info@your websitename.com
      </li>
      <li>
        <svg viewBox="0 0 16 16" aria-hidden="true"><circle cx="8" cy="8" r="6.5" fill="var(--accent)"/><path d="M1.5 8h13M8 1.5c-2.5 3-2.5 10 0 13M8 1.5c2.5 3 2.5 10 0 13" fill="none" stroke="#fff" stroke-width="1"/></svg>
        www.your websitename.com
      </li>
    </ul>
  </section>

  <section class="card card--back" aria-label="Business card back">
    <p class="company-name">528BUILDA</p>
  </section>
</body>
</html>
```